Additional Benefits of Working for VELMAR

Please prepare an infographic on the additional benefits besides salary of working at VELMAR as detailed in the attached word document. Also attached is our logo in eps and our company design "Grounds". We are a Not For Profit company that finds jobs for unemployed people of government benefit payments

Arrowmart Market(s)

Attracting people to work for VELMAR. Making VELMAR an employer of choice.

Font styles to use
Sans Serif

Colors

Designer to choose colors to be used in the design.

Requirements
Must have
• be on 1 page
• have our logo
Nice to have
• Our Grounds design worked into it.
• Happy engaged employees
• Community engagement - we are a not for profit organisation
Should not have
• Discrimination, swearing,

```html
<!DOCTYPE html>
<html lang="en">
<head>
<meta charset="utf-8">
<title>The Benefits of Working with Velmar</title>
<link href="https://fonts.googleapis.com/css2?family=Roboto+Condensed:wght@300;400;700;900&family=Roboto:wght@400;700&display=swap" rel="stylesheet">
<style>
:root{
  --bg:#e9eaeb;
  --teal-dark:#0b3f44;
  --teal-mid:#14646a;
  --green:#8cc63f;
  --green-deep:#6fae2f;
  --label:#1e9a72;
  --ink:#333;
  --grey:#555;
  --divider:#8cc63f;
}
*{box-sizing:border-box;margin:0;padding:0}
html,body{width:1200px;height:1000px;overflow:hidden;background:var(--bg)}
body{position:relative;font-family:"Roboto",Arial,sans-serif;color:var(--ink)}
.poster{position:absolute;top:157px;width:533px;height:686px;background:#fff;overflow:hidden}
.poster--left{left:57px}
.poster--right{left:611px}
.poster__frame{position:absolute;inset:0}
.poster__title{position:absolute;top:18px;left:0;width:100%;text-align:center;color:#fff;font-family:"Roboto Condensed",Arial,sans-serif}
.poster__title-main{display:block;font-weight:900;font-size:44px;line-height:44px;letter-spacing:.5px}
.poster__title-sub{display:block;font-weight:300;font-size:27px;line-height:32px;letter-spacing:.5px}
.column-rule{position:absolute;top:138px;width:2px;height:488px;background:var(--divider)}
.row-rule{position:absolute;height:2px;background:var(--divider)}
.abs{position:absolute;transform:translateX(-50%);text-align:center}
.abs-left{position:absolute;text-align:left}
.heading{font-family:"Roboto Condensed",Arial,sans-serif;font-weight:700;color:var(--green);font-size:21px;line-height:23px;white-space:nowrap}
.heading-and{font-family:"Roboto",Arial,sans-serif;font-size:10px;color:#444;display:flex;align-items:center;gap:6px;justify-content:center}
.heading-and::before,.heading-and::after{content:"";width:44px;height:1px;background:#777}
.label{font-family:"Roboto Condensed",Arial,sans-serif;font-weight:700;color:var(--label);font-size:9.5px;line-height:10.5px;text-transform:uppercase}
.note{font-size:6px;line-height:7px;color:#444}
.big-figure{font-family:"Roboto Condensed",Arial,sans-serif;font-weight:900;font-size:19px;line-height:19px;color:#fff;-webkit-text-stroke:1px var(--label)}
.big-grey{font-family:"Roboto Condensed",Arial,sans-serif;font-weight:900;color:#e4e4e4;-webkit-text-stroke:.8px #555;text-transform:uppercase}
.icon-lg{position:absolute;transform:translateX(-50%)}
.icon-sm{display:block;margin:0 auto 3px}
.thin-rule{height:1px;background:#777;margin:2px 0}
.site-url{position:absolute;left:12px;bottom:14px;color:#fff;font-weight:700;font-size:12.5px}
.brand-name{position:absolute;right:18px;bottom:26px;font-family:"Roboto",Arial,sans-serif;font-weight:700;font-size:38px;color:#2b2b2b;letter-spacing:-1px}
</style>
</head>
<body>

<!-- ===== Poster 1 ===== -->
<section class="poster poster--left">
  <svg class="poster__frame" width="533" height="686" viewBox="0 0 533 686">
    <defs>
      <linearGradient id="groundsA" x1="0" y1="0" x2="1" y2="1">
        <stop offset="0" stop-color="#0b3f44"/><stop offset=".6" stop-color="#12555a"/><stop offset="1" stop-color="#1b6e5a"/>
      </linearGradient>
    </defs>
    <rect width="533" height="150" fill="url(#groundsA)" role="img" aria-label="Grounds pattern artwork in deep teal and green"/>
    <path d="M0 128 Q266 98 533 128 L533 150 L0 150Z" fill="var(--green)"/>
    <path d="M0 140 Q266 108 533 140 L533 160 L0 160Z" fill="#fff"/>
    <path d="M0 606 C90 604 170 656 270 659 C380 662 470 622 533 578 L533 686 L0 686Z" fill="var(--green)"/>
    <path d="M0 626 C90 624 170 674 270 677 C380 680 470 642 533 600 L533 686 L0 686Z" fill="url(#groundsA)" role="img" aria-label="Grounds pattern artwork in deep teal and green"/>
    <ellipse cx="470" cy="680" rx="112" ry="66" fill="#fff"/>
  </svg>
  <h1 class="poster__title"><span class="poster__title-main">THE BENEFITS</span><span class="poster__title-sub">OF WORKING WITH US</span></h1>
  <div class="column-rule" style="left:177px"></div>
  <div class="column-rule" style="left:355px"></div>

  <!-- Life Balance -->
  <svg class="icon-lg" style="left:89px;top:150px" width="80" height="78" viewBox="0 0 80 78">
    <circle cx="40" cy="40" r="36" fill="none" stroke="#333" stroke-width="2" stroke-dasharray="3 3"/>
    <line x1="40" y1="14" x2="40" y2="60" stroke="#333" stroke-width="3"/>
    <line x1="14" y1="26" x2="66" y2="26" stroke="#333" stroke-width="3"/>
    <circle cx="40" cy="12" r="5" fill="#cfd8dc" stroke="#333" stroke-width="2"/>
    <path d="M8 44 L22 32 L36 44Z" fill="#c0392b" stroke="#333" stroke-width="1.5"/>
    <rect x="11" y="44" width="22" height="14" fill="var(--green)" stroke="#333" stroke-width="1.5"/>
    <rect x="46" y="40" width="24" height="18" rx="2" fill="#e67e22" stroke="#333" stroke-width="1.5"/>
    <rect x="30" y="60" width="20" height="4" fill="#333"/>
  </svg>
  <div class="abs heading" style="left:89px;top:238px">Life Balance</div>

  <div class="abs" style="left:48px;top:272px;width:80px">
    <svg class="icon-sm" width="22" height="24" viewBox="0 0 22 24"><path d="M11 2 L18 12 H14 L20 19 H2 L8 12 H4Z" fill="none" stroke="var(--label)" stroke-width="1.5"/><rect x="9" y="19" width="4" height="4" fill="var(--label)"/></svg>
    <div class="label">Velmar<br>Day Leave</div><div class="note">An extra day off at Christmas.</div>
  </div>
  <div class="abs" style="left:133px;top:272px;width:80px">
    <svg class="icon-sm" width="24" height="24" viewBox="0 0 24 24"><rect x="3" y="12" width="18" height="10" fill="none" stroke="var(--label)" stroke-width="1.5"/><path d="M3 16 Q7 13 12 16 T21 16" fill="none" stroke="var(--label)" stroke-width="1.3"/><path d="M8 12V6M12 12V6M16 12V6" stroke="var(--label)" stroke-width="1.5"/></svg>
    <div class="label">Birthday<br>Leave</div><div class="note">A paid day off on<br>your birthday.</div>
  </div>
  <div class="abs" style="left:48px;top:360px;width:84px">
    <svg class="icon-sm" width="26" height="22" viewBox="0 0 26 22"><rect x="2" y="12" width="22" height="6" fill="none" stroke="var(--label)" stroke-width="1.5"/><circle cx="7" cy="9" r="3" fill="var(--label)"/><path d="M2 8V20M24 12V20" stroke="var(--label)" stroke-width="1.5"/><text x="16" y="8" font-size="7" fill="var(--label)" font-weight="700">z</text></svg>
    <div class="label">A Day Off<br>Every Month</div><div class="note">as time in lieu</div>
  </div>
  <div class="abs" style="left:133px;top:366px;width:80px">
    <svg class="icon-sm" width="24" height="36" viewBox="0 0 24 36"><circle cx="12" cy="5" r="4" fill="var(--label)"/><path d="M12 10 L10 22 L6 34 M11 20 L16 34 M11 12 L17 20" stroke="var(--label)" stroke-width="3" fill="none" stroke-linecap="round"/><rect x="2" y="16" width="7" height="10" rx="1" fill="var(--label)"/></svg>
    <div class="label">4 Weeks<br>Annual Leave</div>
  </div>
  <div class="abs" style="left:48px;top:436px;width:84px">
    <svg class="icon-sm" width="24" height="24" viewBox="0 0 24 24"><rect x="4" y="3" width="16" height="18" fill="none" stroke="var(--label)" stroke-width="1.5"/><circle cx="12" cy="10" r="4" fill="none" stroke="var(--label)" stroke-width="1.5"/><path d="M8 17H16" stroke="var(--label)" stroke-width="1.5"/></svg>
    <div class="label">Generous<br>Personal<br>Leave</div>
  </div>
  <div class="abs" style="left:133px;top:468px;width:84px">
    <svg class="icon-sm" width="22" height="28" viewBox="0 0 22 28"><path d="M6 26 V12 L3 6 M6 12 L9 4 M9 12 L13 3 M12 12 L17 6 L18 16 Q18 26 10 26Z" fill="none" stroke="var(--label)" stroke-width="2" stroke-linejoin="round"/></svg>
    <div class="label">Support for<br>Parental<br>Leave</div><div class="note">for the birth or adoption<br>of a child</div>
  </div>
  <div class="abs" style="left:48px;top:514px;width:84px">
    <svg class="icon-sm" width="24" height="24" viewBox="0 0 24 24"><rect x="3" y="3" width="15" height="18" fill="none" stroke="var(--label)" stroke-width="1.5"/><path d="M6 8H15M6 12H15M6 16H11" stroke="var(--label)" stroke-width="1.3"/><path d="M14 18 L22 10" stroke="var(--label)" stroke-width="2"/></svg>
    <div class="label">Flexible Work<br>Arrangements</div>
  </div>

  <!-- Wellbeing -->
  <svg class="icon-lg" style="left:266px;top:147px" width="80" height="70" viewBox="0 0 80 70">
    <path d="M40 66 L8 34 Q0 24 6 14 Q16 0 30 6 Q36 9 40 16 Q44 9 50 6 Q64 0 74 14 Q80 24 72 34Z" fill="var(--green)" stroke="#333" stroke-width="2.5"/>
    <path d="M12 34 H30 L34 26 L40 44 L46 30 L50 34 H68" fill="none" stroke="#333" stroke-width="2.5" stroke-linejoin="round"/>
  </svg>
  <div class="abs heading" style="left:266px;top:238px">Wellbeing</div>

  <div class="abs" style="left:226px;top:320px;width:86px">
    <svg class="icon-sm" width="30" height="26" viewBox="0 0 30 26"><rect x="2" y="8" width="5" height="14" fill="none" stroke="var(--label)" stroke-width="1.5"/><rect x="23" y="8" width="5" height="14" fill="none" stroke="var(--label)" stroke-width="1.5"/><path d="M7 15H23" stroke="var(--label)" stroke-width="2"/><path d="M11 15 V6 Q15 2 19 6 V15" fill="none" stroke="var(--label)" stroke-width="1.5"/></svg>
    <div class="big-figure" style="margin-top:6px">$450</div>
    <div class="label" style="font-size:8px;text-transform:none">per Year</div>
    <div class="note">to spend on</div>
    <div class="label" style="margin-top:2px">Wellbeing<br>Services</div>
    <div class="note">such as gym or<br>yoga membership.</div>
  </div>
  <div class="abs" style="left:306px;top:316px;width:86px">
    <svg class="icon-sm" width="34" height="36" viewBox="0 0 34 36"><circle cx="17" cy="16" r="9" fill="none" stroke="var(--label)" stroke-width="2"/><path d="M5 18 V14 Q5 2 17 2 Q29 2 29 14 V18" fill="none" stroke="var(--label)" stroke-width="2"/><rect x="2" y="13" width="5" height="9" rx="2" fill="var(--label)"/><rect x="27" y="13" width="5" height="9" rx="2" fill="var(--label)"/><path d="M8 34 Q17 26 26 34" fill="none" stroke="var(--label)" stroke-width="2"/></svg>
    <div class="label">Free<br>Counselling<br>Services</div>
    <div class="big-figure" style="margin-top:2px">24X7</div>
    <div class="note">via our Employee<br>Assistance Program</div>
  </div>
  <div class="abs" style="left:226px;top:484px;width:96px">
    <svg class="icon-sm" width="32" height="38" viewBox="0 0 32 38"><path d="M16 2 L29 7 V18 Q29 30 16 36 Q3 30 3 18 V7Z" fill="none" stroke="var(--label)" stroke-width="2"/><path d="M16 12V26M9 19H23" stroke="var(--label)" stroke-width="4"/></svg>
    <div class="label">Discount<br>Private Health<br>Insurance</div>
  </div>
  <div class="abs" style="left:306px;top:484px;width:86px">
    <svg class="icon-sm" width="36" height="32" viewBox="0 0 36 32"><path d="M6 18 Q6 4 18 4 Q30 4 30 18Z" fill="none" stroke="var(--label)" stroke-width="2"/><rect x="2" y="18" width="32" height="4" fill="none" stroke="var(--label)" stroke-width="2"/><path d="M14 4 V14 M22 4 V14" stroke="var(--label)" stroke-width="1.5"/><rect x="8" y="24" width="20" height="6" rx="2" fill="none" stroke="var(--label)" stroke-width="1.5"/></svg>
    <div class="label">WHS Policies</div>
    <div class="note">which support a safe,<br>inclusive work place</div>
  </div>

  <!-- Career Growth -->
  <svg class="icon-lg" style="left:444px;top:146px" width="74" height="76" viewBox="0 0 74 76">
    <path d="M8 74 V58 H22 V44 H36 V30 H50 V16 H64 V74Z" fill="#bdbdbd" stroke="#333" stroke-width="2"/>
    <path d="M4 54 L4 44 H18 V30 H32 V16" fill="none" stroke="#4aa3df" stroke-width="2.5"/>
    <path d="M28 20 L32 14 L36 20" fill="none" stroke="#4aa3df" stroke-width="2.5"/>
    <line x1="60" y1="16" x2="60" y2="2" stroke="#333" stroke-width="2"/>
    <path d="M60 2 H70 L67 6 L70 10 H60Z" fill="#e74c3c"/>
  </svg>
  <div class="abs heading" style="left:444px;top:238px">Career Growth</div>
  <div class="abs heading-and" style="left:444px;top:263px;width:150px">and</div>
  <div class="abs heading" style="left:444px;top:278px">Professional</div>
  <div class="abs heading" style="left:444px;top:304px">Development</div>

  <div class="abs" style="left:404px;top:372px;width:82px">
    <svg class="icon-sm" width="30" height="32" viewBox="0 0 30 32"><rect x="12" y="2" width="16" height="12" fill="none" stroke="var(--label)" stroke-width="1.5"/><circle cx="7" cy="8" r="3" fill="var(--label)"/><path d="M7 12 V22 L4 30 M7 22 L10 30 M7 14 L14 10" stroke="var(--label)" stroke-width="2.4" fill="none"/><path d="M20 14 V28 M16 28 H24" stroke="var(--label)" stroke-width="1.5"/></svg>
    <div class="label">Ongoing<br>Internal<br>Training &amp;<br>Development<br>Opportunities</div>
  </div>
  <div class="abs" style="left:486px;top:345px;width:82px">
    <svg class="icon-sm" width="28" height="28" viewBox="0 0 28 28"><circle cx="12" cy="12" r="9" fill="none" stroke="var(--label)" stroke-width="2"/><path d="M18 18 L26 26" stroke="var(--label)" stroke-width="3.5"/><path d="M7 10 Q12 6 16 12" fill="none" stroke="var(--label)" stroke-width="1.5"/></svg>
    <div class="label">External<br>Study<br>Support &amp;<br>Study Leave</div>
  </div>
  <div class="abs" style="left:486px;top:432px;width:82px">
    <svg class="icon-sm" width="26" height="24" viewBox="0 0 26 24"><path d="M2 22 H8 V16 H14 V10 H20 V4 H24" fill="none" stroke="var(--label)" stroke-width="2"/><circle cx="11" cy="7" r="2.5" fill="var(--label)"/></svg>
    <div class="label">Career<br>Advancement<br>Opportunities</div>
  </div>
  <div class="abs" style="left:404px;top:480px;width:82px">
    <svg class="icon-sm" width="28" height="34" viewBox="0 0 28 34"><circle cx="14" cy="12" r="8" fill="none" stroke="var(--label)" stroke-width="2"/><path d="M10 20 V26 H18 V20" fill="none" stroke="var(--label)" stroke-width="2"/><path d="M11 29 H17 M12 32 H16" stroke="var(--label)" stroke-width="1.8"/><path d="M14 0 V3 M3 4 L5 6 M25 4 L23 6" stroke="var(--label)" stroke-width="1.5"/></svg>
    <div class="label">Access to<br>the Tools &amp;<br>Technology</div>
    <div class="note">to do your job well</div>
  </div>
  <div class="abs" style="left:486px;top:496px;width:82px">
    <svg class="icon-sm" width="24" height="28" viewBox="0 0 24 28"><rect x="3" y="3" width="18" height="23" fill="none" stroke="var(--label)" stroke-width="1.8"/><circle cx="12" cy="11" r="3" fill="var(--label)"/><path d="M7 20 Q12 14 17 20Z" fill="var(--label)"/></svg>
    <div class="label">Internal<br>Job Vacancy<br>Listings</div>
  </div>

  <div class="site-url">www.velmar.org.au</div>
  <div class="brand-name">velmar</div>
</section>

<!-- ===== Poster 2 ===== -->
<section class="poster poster--right">
  <svg class="poster__frame" width="533" height="686" viewBox="0 0 533 686">
    <defs>
      <linearGradient id="groundsB" x1="0" y1="0" x2="1" y2="1">
        <stop offset="0" stop-color="#0b3f44"/><stop offset=".6" stop-color="#12555a"/><stop offset="1" stop-color="#1b6e5a"/>
      </linearGradient>
    </defs>
    <rect width="533" height="150" fill="url(#groundsB)" role="img" aria-label="Grounds pattern artwork in deep teal and green"/>
    <path d="M0 128 Q266 98 533 128 L533 150 L0 150Z" fill="var(--green)"/>
    <path d="M0 140 Q266 108 533 140 L533 160 L0 160Z" fill="#fff"/>
    <path d="M0 606 C90 604 170 656 270 659 C380 662 470 622 533 578 L533 686 L0 686Z" fill="var(--green)"/>
    <path d="M0 626 C90 624 170 674 270 677 C380 680 470 642 533 600 L533 686 L0 686Z" fill="url(#groundsB)" role="img" aria-label="Grounds pattern artwork in deep teal and green"/>
    <ellipse cx="470" cy="680" rx="112" ry="66" fill="#fff"/>
  </svg>
  <h1 class="poster__title"><span class="poster__title-main">THE BENEFITS</span><span class="poster__title-sub">OF WORKING WITH US</span></h1>
  <div class="column-rule" style="left:177px"></div>
  <div class="column-rule" style="left:354px"></div>
  <div class="row-rule" style="left:0;top:434px;width:178px"></div>
  <div class="row-rule" style="left:178px;top:377px;width:177px"></div>

  <!-- Remuneration -->
  <svg class="icon-lg" style="left:89px;top:148px" width="80" height="66" viewBox="0 0 80 66">
    <path d="M4 26 L40 2 L76 26 V64 H4Z" fill="#d9d9d9" stroke="#333" stroke-width="2.5"/>
    <rect x="16" y="12" width="48" height="34" fill="var(--green)" stroke="#333" stroke-width="2"/>
    <text x="40" y="37" text-anchor="middle" font-family="Roboto" font-weight="700" font-size="20" fill="#fff">$</text>
    <path d="M4 26 L40 48 L76 26 V64 H4Z" fill="#fff" stroke="#333" stroke-width="2.5"/>
  </svg>
  <div class="abs heading" style="left:89px;top:227px">Remuneration</div>
  <div class="abs heading-and" style="left:89px;top:251px;width:150px">and</div>
  <div class="abs heading" style="left:89px;top:266px">Salary Packaging</div>

  <svg style="position:absolute;left:20px;top:300px" width="26" height="30" viewBox="0 0 26 30"><path d="M2 28 L10 20 L14 24 L24 12" fill="none" stroke="var(--label)" stroke-width="1.8"/><circle cx="17" cy="8" r="6" fill="none" stroke="var(--label)" stroke-width="1.5"/><text x="17" y="11" font-size="8" text-anchor="middle" fill="var(--label)" font-weight="700">$</text></svg>
  <div class="abs-left label" style="left:62px;top:314px">Competitive Salary</div>

  <svg style="position:absolute;left:16px;top:336px" width="32" height="34" viewBox="0 0 32 34"><path d="M6 14 L16 4 L26 14 V26 H6Z" fill="none" stroke="var(--label)" stroke-width="1.6"/><rect x="13" y="18" width="6" height="8" fill="var(--label)"/><path d="M2 30 Q10 26 18 30 H30" fill="none" stroke="var(--label)" stroke-width="1.6"/></svg>
  <div class="abs-left" style="left:62px;top:331px;width:110px">
    <div class="label"><span class="note" style="font-weight:400;text-transform:none;color:#444">Ability to</span> Salary Package</div>
    <div class="big-figure">$15,900</div>
    <div class="label">&amp; Reduce Your Tax</div>
    <div class="note">Package rent, home loans, child care<br>and much more.</div>
  </div>

  <svg style="position:absolute;left:16px;top:390px" width="30" height="34" viewBox="0 0 30 34"><circle cx="15" cy="11" r="9" fill="none" stroke="var(--label)" stroke-width="1.6"/><text x="15" y="15" font-size="11" text-anchor="middle" fill="var(--label)" font-weight="700">$</text><path d="M2 30 Q10 24 18 28 H28" fill="none" stroke="var(--label)" stroke-width="1.6"/></svg>
  <div class="abs-left" style="left:62px;top:387px;width:110px">
    <div class="label">Salary Package</div>
    <div class="big-figure">$2,650</div>
    <div class="note">on meal, entertainment and holiday<br>accomodation.</div>
  </div>

  <!-- Recognition -->
  <svg class="icon-lg" style="left:89px;top:440px" width="54" height="74" viewBox="0 0 54 74">
    <path d="M12 2 L24 30 M42 2 L30 30" stroke="var(--green-deep)" stroke-width="8"/>
    <circle cx="27" cy="48" r="22" fill="#5a5a5a" stroke="#333" stroke-width="2"/>
    <circle cx="27" cy="48" r="15" fill="#fff" stroke="#333" stroke-width="1.5"/>
    <path d="M27 38 L30 45 L37 45 L31.5 49.5 L33.5 57 L27 52.5 L20.5 57 L22.5 49.5 L17 45 L24 45Z" fill="#e67e22"/>
  </svg>
  <div class="abs heading" style="left:89px;top:516px">Recognition</div>
  <div class="abs" style="left:89px;top:541px;width:150px">
    <div class="note">We celebrate our people for</div>
    <div class="label">Reaching Service<br>Milestones</div>
    <div class="thin-rule"></div>
    <div class="label">Team &amp; Individual<br>Recognition</div>
    <div class="note">for high performance</div>
  </div>

  <!-- Benefits -->
  <svg class="icon-lg" style="left:266px;top:146px" width="96" height="76" viewBox="0 0 96 76">
    <circle cx="48" cy="16" r="14" fill="var(--green)" stroke="#333" stroke-width="2"/>
    <path d="M48 8V24M40 16H56" stroke="#333" stroke-width="4"/>
    <circle cx="22" cy="10" r="6" fill="none" stroke="var(--green)" stroke-width="2"/>
    <circle cx="74" cy="10" r="6" fill="none" stroke="var(--green)" stroke-width="2"/>
    <path d="M8 30 Q6 50 22 60 L34 68 V74 M88 30 Q90 50 74 60 L62 68 V74" fill="none" stroke="#333" stroke-width="2.2"/>
    <path d="M10 30 Q12 46 26 54 L38 62 Q42 56 36 50 L28 44" fill="#f5c29b" stroke="#333" stroke-width="2"/>
    <path d="M86 30 Q84 46 70 54 L58 62 Q54 56 60 50 L68 44" fill="#f5c29b" stroke="#333" stroke-width="2"/>
  </svg>
  <div class="abs heading" style="left:266px;top:230px">Benefits</div>

  <svg style="position:absolute;left:189px;top:262px" width="34" height="44" viewBox="0 0 34 44"><rect x="2" y="2" width="30" height="40" fill="none" stroke="var(--label)" stroke-width="1.5" stroke-dasharray="3 2"/><circle cx="10" cy="14" r="4" fill="none" stroke="var(--label)" stroke-width="1.5"/><circle cx="10" cy="28" r="4" fill="none" stroke="var(--label)" stroke-width="1.5"/><path d="M13 16 L26 28 M13 26 L26 14" stroke="var(--label)" stroke-width="1.5"/><rect x="22" y="20" width="8" height="20" fill="var(--green)"/></svg>
  <div class="abs-left" style="left:243px;top:263px;width:105px">
    <div class="label">Discounted<br>Vouchers</div>
    <div class="note">for Corvin, Greenfield's, Tonebox,<br>Reelhouse, Cellar Co, ValueMart,<br>Arrowmart, Camp Depot and many others<br>via Paywell E-Wallet</div>
  </div>

  <svg style="position:absolute;left:189px;top:323px" width="34" height="26" viewBox="0 0 34 26"><rect x="2" y="2" width="30" height="22" rx="2" fill="none" stroke="var(--label)" stroke-width="1.8"/><circle cx="11" cy="11" r="3.5" fill="var(--label)"/><path d="M6 20 Q11 14 16 20Z" fill="var(--label)"/><path d="M19 9H28M19 13H28M19 17H25" stroke="var(--label)" stroke-width="1.5"/></svg>
  <div class="abs-left" style="left:243px;top:322px;width:108px">
    <div class="label">A Range of Other<br>Employee Discounts</div>
    <div class="note">are also available, including access<br>to discounted banking and finance,<br>vehicle purchasing, leasing and<br>hotel accommodation.</div>
  </div>

  <!-- Contributing to Community -->
  <svg class="icon-lg" style="left:266px;top:388px" width="86" height="84" viewBox="0 0 86 84">
    <circle cx="43" cy="12" r="8" fill="#f1c40f" stroke="#333" stroke-width="1.5"/>
    <path d="M28 36 Q28 22 43 22 Q58 22 58 36" fill="var(--green)" stroke="#333" stroke-width="1.5"/>
    <circle cx="14" cy="48" r="8" fill="#4aa3df" stroke="#333" stroke-width="1.5"/>
    <path d="M2 78 Q4 60 20 60 L26 68" fill="#4aa3df" stroke="#333" stroke-width="1.5"/>
    <circle cx="72" cy="48" r="8" fill="#e67e22" stroke="#333" stroke-width="1.5"/>
    <path d="M84 78 Q82 60 66 60 L60 68" fill="#e67e22" stroke="#333" stroke-width="1.5"/>
    <path d="M26 74 H60" stroke="#4aa3df" stroke-width="5"/>
  </svg>
  <div class="abs heading" style="left:266px;top:480px">Contributing to</div>
  <div class="abs heading" style="left:266px;top:503px">Community</div>
  <div class="abs" style="left:266px;top:530px;width:155px">
    <div class="note">Team involvement in</div>
    <div class="label">Local Charity &amp; Community<br>Events</div>
    <div class="thin-rule"></div>
    <div class="note">Participation in</div>
    <div class="label">Velmar's 1000 Jobs</div>
    <div class="note">in 100 Days Initiative</div>
    <div class="thin-rule"></div>
    <div class="label">Strong Relationships &amp;<br>Connection</div>
    <div class="note">with Indigenous Communities in Support of<br>Indigenous Employment.</div>
  </div>

  <!-- Diversity and Inclusion -->
  <svg class="icon-lg" style="left:444px;top:150px" width="110" height="100" viewBox="0 0 110 100">
    <rect x="2" y="8" width="18" height="30" transform="rotate(-45 11 23)" fill="#4aa3df" stroke="#333" stroke-width="2"/>
    <rect x="88" y="8" width="18" height="30" transform="rotate(45 97 23)" fill="var(--green)" stroke="#333" stroke-width="2"/>
    <path d="M22 30 L52 60 Q60 66 66 58 L50 40Z" fill="#e8b88f" stroke="#333" stroke-width="2"/>
    <path d="M88 30 L58 60 Q50 66 44 58 L60 40 Q64 34 70 36Z" fill="#6d4c3d" stroke="#333" stroke-width="2"/>
    <rect x="4" y="64" width="18" height="30" transform="rotate(45 13 79)" fill="#4aa3df" stroke="#333" stroke-width="2"/>
    <rect x="86" y="64" width="18" height="30" transform="rotate(-45 95 79)" fill="var(--green)" stroke="#333" stroke-width="2"/>
    <path d="M26 74 L44 56 L62 60 L40 84Z" fill="#e8b88f" stroke="#333" stroke-width="2"/>
  </svg>
  <div class="abs heading" style="left:444px;top:271px">Diversity</div>
  <div class="abs heading-and" style="left:444px;top:293px;width:150px">and</div>
  <div class="abs heading" style="left:444px;top:303px">Inclusion</div>

  <svg class="icon-lg" style="left:444px;top:338px" width="48" height="48" viewBox="0 0 48 48">
    <g fill="var(--label)"><circle cx="24" cy="6" r="4"/><circle cx="42" cy="24" r="4"/><circle cx="24" cy="42" r="4"/><circle cx="6" cy="24" r="4"/></g>
    <circle cx="24" cy="24" r="14" fill="none" stroke="var(--label)" stroke-width="4" stroke-dasharray="14 8"/>
  </svg>
  <div class="abs" style="left:444px;top:397px;width:160px">
    <div class="label">An Inclusive &amp; Diverse<br>Culture</div>
    <div class="note">where different backgrounds, experience and<br>perspectives are valued</div>
  </div>

  <svg class="icon-lg" style="left:444px;top:440px" width="60" height="48" viewBox="0 0 60 48">
    <circle cx="18" cy="16" r="11" fill="none" stroke="var(--label)" stroke-width="4"/>
    <path d="M18 27 V44 M11 37 H25" stroke="var(--label)" stroke-width="4"/>
    <circle cx="42" cy="16" r="11" fill="none" stroke="var(--label)" stroke-width="4"/>
    <path d="M42 27 V44 M35 37 H49" stroke="var(--label)" stroke-width="4"/>
  </svg>
  <div class="abs" style="left:444px;top:494px;width:170px">
    <div class="label" style="color:#444">Gender Diversity</div>
    <div class="big-grey" style="font-size:22px;line-height:22px;margin-top:3px">Over 50%</div>
    <div class="big-grey" style="font-size:13px;line-height:14px">Of our workforce<br>&amp; our leaders<br>are female.</div>
  </div>

  <div class="site-url">www.velmar.org.au</div>
  <div class="brand-name">velmar</div>
</section>

</body>
</html>
```